Spanish Student Needs a Cover for his PhD Dissertation

Hi everyone :) So, I'm a Corneal surgeon currently finishing my PhD, with a dissertation focused on the evaluation of quality of life in patients affected by a disease called Keratoconus. Just so you know, Keratoconus is a condition in which the cornea (the frontal part of the way) gets thin and bulgy and it decreases vision. What I did during my PhD was designing a questionnaire for evaluating quality of life in this kind of patients.
I need to design a hard cover for my dissertation, which is 200 sheets long. I like kind of minimalistic and geometric designs but I am totally open to suggestions. What needs to be in the cover is the name of the dissertation "Diseño, desarrollo y validación de una encuesta para evaluar el compromiso visual y emocional subjetivos en pacientes con Queratocono" and my name, "Iker Zurmendi". The other thing that needs to go there is the logo of my university (Universidad de Montehierro). Aside from that, anything else is up to the designer. It would be important to use the kind of "red" color I am using in the dissertation. I am attaching the frontal page of my dissertation so you know what kind of design and colors I am using.
In the back part, of the cover, there should be this small inscription: "Iker Zurmendi, MD, es un Oftalmólogo Subespecialista en Cirugía Refractiva de la Universidad Tecnológica Cordillerana (Colombia) y la Universidad de Montehierro (España). Actualmente se desempeña como miembro del Departamento de Córnea y Cirugía Refractiva de la Clínica de Oftalmología Miraluz y como director de su propia compañía de emprendimiento médico Silver Heron Surgical". Please leave a space to place my picture; I will have it taken this week so I don't have it right now, you can just leave the blank spot and I will include it later
The size of the pages is standard "letter" size.
Thanks a lot!

Target Market(s)

PhD Scholars

Font styles to use
Serif

Requirements
Must have
• The "red" color I use on my font. It must be formal but "young".
Nice to have
• I like to keep the design clean, kind of "formal with a young" touch so to speak. I really like gray colors, so it would be nice to have broad areas of gray. I love geometrical designs.
I have uploaded a very early version a friend of mine made (it even had a different title); this can be a starting point for you to work on, but I am more than open to suggestions and new ideas.
Should not have
• Please don't use my whole name, Iker Zurmendi is fine. I don't like ALL CAPITALS.

```html
<!DOCTYPE html>
<html lang="es">
<head>
<meta charset="utf-8">
<title>Diseño, desarrollo y validación — Cubierta</title>
<link rel="stylesheet" href="https://fonts.googleapis.com/css2?family=Playfair+Display:wght@400;700;900&family=Tinos:wght@400;700&display=swap">
<style>
  :root {
    --stage: #000000;
    --cover-red: #c8161d;
    --paper: #ffffff;
    --ink: #111111;
  }
  * { margin: 0; padding: 0; box-sizing: border-box; }
  html, body { width: 1200px; height: 1200px; overflow: hidden; background: var(--stage); }
  .canvas { position: relative; width: 1200px; height: 1200px; }

  .spread { position: absolute; left: 50px; top: 253px; width: 1099px; height: 694px; background: var(--cover-red); overflow: hidden; }

  /* back cover */
  .back-copy { position: absolute; left: 46px; top: 49px; width: 446px; color: var(--paper);
    font-family: "Tinos", serif; font-size: 8.6px; line-height: 12.6px; text-align: justify; }
  .back-copy p { margin-bottom: 4px; }
  .author-photo { position: absolute; left: 211px; top: 360px; width: 118px; height: 118px; border-radius: 50%;
    background: var(--paper); display: flex; align-items: center; justify-content: center;
    font-family: "Playfair Display", serif; font-size: 15px; color: var(--ink); }
  .author-bio { position: absolute; left: 46px; top: 502px; width: 446px; color: var(--paper);
    font-family: "Tinos", serif; font-size: 8.6px; line-height: 12.8px; text-align: justify; }

  /* spine */
  .spine-mark { position: absolute; left: 542px; top: 149px; }
  .spine-title { position: absolute; left: 562px; top: 196px; width: 246px; transform-origin: left top;
    transform: rotate(90deg); color: var(--paper); font-family: "Tinos", serif; font-size: 7.2px;
    line-height: 8.6px; text-align: center; }
  .spine-author { position: absolute; left: 560px; top: 526px; transform-origin: left top; transform: rotate(90deg);
    color: var(--paper); font-family: "Playfair Display", serif; font-size: 11px; line-height: 14px; white-space: nowrap; }

  /* front cover */
  .front { position: absolute; left: 562px; top: 0; width: 537px; height: 622px; background: var(--paper); }
  .university { position: absolute; left: 0; top: 31px; width: 100%; text-align: center; }
  .university-dot { display: block; width: 45px; height: 45px; margin: 0 auto 5px; border-radius: 50%;
    border: 2px solid var(--cover-red); }
  .university-name { font-family: "Tinos", serif; font-weight: 700; font-size: 10px; color: var(--cover-red); }
  .emblem { position: absolute; left: 160px; top: 105px; }
  .title { font-family: "Playfair Display", serif; color: var(--ink); font-weight: 400; }
  .title span { position: absolute; left: 0; width: 100%; text-align: center; white-space: nowrap; }
  .title-lead { top: 286px; font-size: 88px; font-weight: 900; color: var(--cover-red); line-height: 90px;
    letter-spacing: -1px; padding-left: 26px; }
  .title-light { font-size: 22px; line-height: 30px; }
  .title-bold { font-size: 25px; font-weight: 700; line-height: 30px; letter-spacing: -0.4px; }
  .line-2 { top: 373px; }
  .line-3 { top: 406px; }
  .line-4 { top: 441px; }
  .line-5 { top: 476px; }
  .title-large { top: 508px; font-size: 35px; line-height: 40px; }
  .title-disease { top: 552px; font-size: 43px; font-weight: 700; color: var(--cover-red); line-height: 48px;
    letter-spacing: -1px; }
  .front-author { position: absolute; left: 562px; top: 630px; width: 537px; text-align: center; color: var(--paper);
    font-family: "Playfair Display", serif; font-size: 36px; line-height: 46px; letter-spacing: 4px; }
</style>
</head>
<body>
<div class="canvas">
  <div class="spread">
    <section class="back-cover">
      <div class="back-copy">
        <p>Lorem ipsum dolor sit amet, consectetuer adipiscing elit, sed diam nonummy nibh euismod tincidunt ut laoreet dolore magna aliquam erat volutpat. Ut wisi enim ad minim veniam, quis nostrud exerci tation ullamcorper suscipit lobortis nisl ut aliquip ex ea commodo consequat. Duis autem vel eum iriure dolor in hendrerit in vulputate velit esse molestie consequat, vel illum dolore eu feugiat nulla facilisis at vero eros et accumsan et iusto odio dignissim qui blandit praesent luptatum zzril delenit augue duis dolore te feugait nulla facilisi.</p>
        <p>Lorem ipsum dolor sit amet, cons ectetuer adipiscing elit, sed diam nonummy nibh euismod tincidunt ut laoreet dolore magna aliquam erat volutpat. Ut wisi enim ad minim veniam, quis nostrud exerci tation ullamcorper suscipit lobortis nisl ut aliquip ex ea commodo consequat.</p>
        <p>Lorem ipsum dolor sit amet, consectetuer adipiscing elit, sed diam nonummy nibh euismod tincidunt ut laoreet dolore magna aliquam erat volutpat. Ut wisi enim ad minim veniam, quis nostrud exerci tation ullamcorper suscipit lobortis nisl ut aliquip ex ea commodo consequat. Duis autem vel eum iriure dolor in hendrerit in vulputate velit esse molestie consequat, vel illum dolore eu feugiat nulla facilisis at vero eros et accumsan et iusto odio dignissim qui blandit praesent luptatum zzril delenit augue duis dolore te feugait nulla facilisi.</p>
        <p>Lorem ipsum dolor sit amet, cons ectetuer adipiscing elit, sed diam nonummy nibh euismod tincidunt ut laoreet dolore magna aliquam erat volutpat. Ut wisi enim ad minim veniam, quis nostrud exerci tation ullamcorper suscipit lobortis nisl ut aliquip ex ea commodo consequat.</p>
        <p>Lorem ipsum dolor sit amet, consectetuer adipiscing elit, sed diam nonummy nibh euismod tincidunt ut laoreet dolore magna aliquam erat volutpat. Ut wisi enim ad minim veniam, quis nostrud exerci tation ullamcorper suscipit lobortis nisl ut aliquip ex ea commodo consequat. Duis autem vel eum iriure dolor in hendrerit in vulputate velit esse molestie consequat, vel illum dolore eu feugiat nulla facilisis at vero eros et accumsan et iusto odio dignissim qui blandit praesent luptatum zzril delenit augue duis dolore te feugait nulla facilisi.</p>
        <p>Lorem ipsum dolor sit amet, cons ectetuer adipiscing elit, sed diam nonummy nibh euismod tincidunt ut laoreet</p>
      </div>
      <div class="author-photo">authors photo</div>
      <p class="author-bio">Iker Zurmendi, MD, es un Oftalmólogo Subespecialista en Cirugía Refractiva de la Universidad Tecnológica Cordillerana (Colombia) y la Universidad de Montehierro (España). Actualmente se desempeña como miembro del Departamento de Córnea y Cirugía Refractiva de la Clínica de Oftalmología Miraluz y como director de su propia compañía de emprendimiento médico Silver Heron Surgical</p>
    </section>

    <section class="spine">
      <svg class="spine-mark" width="18" height="18" viewBox="0 0 18 18" role="img" aria-label="Emblema ocular en miniatura">
        <polygon points="1,2 17,2 9,17" fill="var(--paper)"/>
      </svg>
      <p class="spine-title">Diseño, desarrollo y validación de una encuesta para evaluar el compromiso visual y emocional subjetivos en pacientes con Queratocono</p>
      <p class="spine-author">Iker Zurmendi</p>
    </section>

    <section class="front">
      <div class="university">
        <span class="university-dot"></span>
        <span class="university-name">Universidad de Montehierro</span>
      </div>
      <svg class="emblem" width="217" height="190" viewBox="0 0 217 190" role="img" aria-label="Ilustración geométrica: triángulo rojo con un ojo estilizado">
        <polygon points="0,0 217,0 108.5,190" fill="var(--cover-red)"/>
      </svg>
      <h1 class="title">
        <span class="title-lead">Diseño,</span>
        <span class="title-light line-2">desarrollo y validación</span>
        <span class="title-bold line-3">de una encuesta para</span>
        <span class="title-bold line-4">evaluar el compromiso visual</span>
        <span class="title-light line-5">y emocional subjetivos</span>
        <span class="title-large">en pacientes con</span>
        <span class="title-disease">QUERATOCONO</span>
      </h1>
    </section>
    <p class="front-author">Iker Zurmendi</p>
  </div>
</div>
</body>
</html>
```